Display wall/splashback design

We are looking at a design to suit the background display/splashback wall of our instore showroom displays needs to be in suttle colours that do not detract from the appliances attached to this wall.
Most of the rangehoods on display are of a stainless colour hence the background cannot have strong solid colours that will attract the eye of the customer away from the products .
One of the main features of our rangehoods is their silence, so something to highlites silence/quiet would be most appropiate.
Sixe is 1.8 metres in height x 6 metres in length

Target Market(s)

High end consumer, women between 25 and 50

Industry/Entity Type

Retail

Requirements
Must have
• An overall gently/quiet and enviromentally friendly look.
A background that inhances the product displayed upon it.

Should not have
• Strong or dominant images nor strong or dominant colours

```html
<!DOCTYPE html>
<html lang="en">
<head>
<meta charset="utf-8">
<title>Showroom Splashback Wall</title>
<link rel="stylesheet" href="https://fonts.googleapis.com/css2?family=Lato&display=swap">
<style>
  :root {
    --sky-aqua: #b3ffff;
    --glow-lime: #d4f0a0;
    --glow-soft: #c8f4b8;
    --rail-amber: #c8900a;
  }
  html, body {
    margin: 0;
    padding: 0;
    overflow: hidden;
    font-family: "Lato", sans-serif;
  }
  .splashback {
    position: relative;
    width: 1200px;
    height: 444px;
    background: var(--sky-aqua);
    overflow: hidden;
  }
  .horizon-glow {
    position: absolute;
    left: 0;
    width: 100%;
  }
  .horizon-glow--upper {
    top: 270px;
    height: 90px;
    background: linear-gradient(to bottom, rgba(212,240,160,0) 0%, var(--glow-lime) 75%, var(--glow-lime) 100%);
  }
  .horizon-glow--lower {
    top: 340px;
    height: 104px;
    background: linear-gradient(to bottom, var(--glow-soft) 0%, var(--glow-lime) 50%, var(--glow-soft) 100%);
  }
  .rail {
    position: absolute;
    left: 0;
    width: 100%;
    height: 11px;
    background: var(--rail-amber);
    box-shadow: 0 0 6px rgba(200,144,10,0.35);
  }
  .rail--upper { top: 333px; }
  .rail--lower { top: 400px; }
  .base-fade {
    position: absolute;
    left: 0;
    top: 418px;
    width: 100%;
    height: 26px;
    background: linear-gradient(to bottom, var(--glow-soft), var(--sky-aqua));
  }
</style>
</head>
<body>
  <main class="splashback">
    <div class="horizon-glow horizon-glow--upper"></div>
    <div class="horizon-glow horizon-glow--lower"></div>
    <div class="base-fade"></div>
    <div class="rail rail--upper"></div>
    <div class="rail rail--lower"></div>
  </main>
</body>
</html>
```